Business Card Design

We need a business card designed for our new company. Prefer a black card with white logo & writing.

Contact Information for Business Card

Ted Galloway, address: 7-4812 Fernhollow Road, Abbotsford, BC, V3K 8R2, Office Phone: 604-712-3390, Cell: 604-947-2164, Email: ted@resinworkshub.ca

Colors

Designer to choose only greyscale colors for use in the design.

```html
<!DOCTYPE html>
<html lang="en">
<head>
<meta charset="utf-8">
<title>Resin Works Hub – Business Card</title>
<link href="https://fonts.googleapis.com/css2?family=Poppins:wght@300;400;700&display=swap" rel="stylesheet">
<style>
  :root{
    --stage:#2a2a2c;
    --card-black:#1d1d1f;
    --pattern-tone:#2c2c2f;
    --ink:#111111;
    --paper:#ffffff;
    --muted:#d9d9d9;
  }
  *{margin:0;padding:0;box-sizing:border-box}
  html,body{width:1200px;height:711px;overflow:hidden;background:var(--stage);font-family:"Poppins",sans-serif}
  .stage{position:relative;width:1200px;height:711px}
  .card{position:absolute;top:201px;width:540px;height:309px;border-radius:6px;overflow:hidden;box-shadow:0 18px 40px rgba(0,0,0,.55)}
  .card--front{left:40px;background:var(--card-black)}
  .card--back{left:620px;background:var(--card-black)}

  .pattern{position:absolute;inset:0;background:radial-gradient(ellipse at 60% 30%,var(--pattern-tone),var(--card-black) 75%)}
  .brand{position:absolute;display:flex;align-items:center;gap:12px;color:var(--paper);font-weight:700;letter-spacing:.02em;white-space:nowrap}
  .brand__dot{width:14px;height:14px;border-radius:50%;background:var(--paper);flex:none}
  .card--front .brand{left:50%;top:50%;transform:translate(-50%,-50%);font-size:40px}

  .mountain{position:absolute;inset:0;background:linear-gradient(128deg,var(--paper) 0%,var(--paper) 30%,#8a8a8a 40%,var(--card-black) 52%,var(--card-black) 100%)}
  .holder{position:absolute;left:30px;top:44px;color:var(--ink)}
  .holder__name{font-size:32px;line-height:1.1;font-weight:300}
  .holder__name strong{font-weight:700}
  .holder__role{font-size:12px;margin-top:4px;font-weight:400}
  .card--back .brand{left:38px;bottom:36px;font-size:24px}

  .contact{position:absolute;right:26px;top:118px;color:var(--paper);font-size:12.5px;font-weight:300;line-height:1.5}
  .contact__address{margin-bottom:10px}
  .contact__list{list-style:none}
  .contact__item{display:flex;align-items:center;gap:8px}
  .contact__icon{width:12px;height:12px;flex:none;fill:none;stroke:var(--paper);stroke-width:1.6}
</style>
</head>
<body>
<main class="stage">
  <section class="card card--front">
    <div class="pattern" role="img" aria-label="Repeating faint brand pattern on black"></div>
    <div class="brand"><span class="brand__dot"></span>Resin Works Hub</div>
  </section>

  <section class="card card--back">
    <div class="mountain" role="img" aria-label="Black mountain silhouette rising across a white sky"></div>
    <div class="holder">
      <p class="holder__name"><strong>Ted</strong> Galloway</p>
      <p class="holder__role">Founder &amp; CEO</p>
    </div>
    <div class="brand"><span class="brand__dot"></span>Resin Works Hub</div>
    <div class="contact">
      <p class="contact__address">7-4812 Fernhollow Road,<br>Abbotsford, BC, V3K 8R2.</p>
      <ul class="contact__list">
        <li class="contact__item"><svg class="contact__icon" viewBox="0 0 12 12"><path d="M2 1.5l2 0 1 2.5-1.3 1a6 6 0 0 0 3.3 3.3l1-1.3 2.5 1v2a1 1 0 0 1-1 1A9 9 0 0 1 1 2.5a1 1 0 0 1 1-1z"/></svg>604-712-3390,</li>
        <li class="contact__item"><svg class="contact__icon" viewBox="0 0 12 12"><rect x="3" y="1" width="6" height="10" rx="1"/><path d="M5.5 9h1"/></svg>604-947-2164,</li>
        <li class="contact__item"><svg class="contact__icon" viewBox="0 0 12 12"><circle cx="6" cy="6" r="5"/><path d="M1 6h10M6 1c2 2 2 8 0 10M6 1c-2 2-2 8 0 10"/></svg>www.resinworkshub.ca</li>
        <li class="contact__item"><svg class="contact__icon" viewBox="0 0 12 12"><rect x="1" y="2.5" width="10" height="7" rx="1"/><path d="M1 3l5 4 5-4"/></svg>ted@resinworkshub.ca</li>
      </ul>
    </div>
  </section>
</main>
</body>
</html>
```